Business Card - connecting 2 souls and beggining the journey of self discovery

Logo on the front
with tag line

On the back list of services and contact details

Seminars
workshops
Coaching
podcasts

Darren Whitlow
Health & Wellbeing Life Coach
0491 372 615
darren@brightcoreliving.example
brightcoreliving.example

Industry/Entity Type

Life Coaching

Contact Information for Business Card

I like the use of colour from the logo to be used. I'm not a fan of white.

Requirements
Must have
• My tagline: The journey home starts with you
Nice to have
• Use of colour that is in the mind body soul logo

```html
<!DOCTYPE html>
<html lang="en">
<head>
<meta charset="utf-8">
<title>Brightcore Living – Business Card</title>
<link rel="stylesheet" href="https://fonts.googleapis.com/css2?family=Poppins:wght@300;400;500;600&display=swap">
<style>
  :root {
    --canvas: #8c8c8c;
    --card-dark: #231f20;
    --card-deep: #1c1a1b;
    --teal: #1a9a86;
    --teal-band: #21a08c;
    --white: #ffffff;
    --name-dark: #263330;
  }
  * { margin: 0; padding: 0; box-sizing: border-box; }
  html, body { width: 1200px; height: 1200px; overflow: hidden; }
  body {
    background: var(--canvas);
    font-family: "Poppins", sans-serif;
    position: relative;
  }
  .card {
    position: absolute;
    left: 120px;
    width: 960px;
    height: 542px;
    overflow: hidden;
    color: var(--white);
  }
  .card--back { top: 38px; background: var(--card-dark); }
  .card--front { top: 620px; background: var(--card-deep); }

  /* back side */
  .name-band {
    position: absolute;
    left: 0; top: 100px;
    width: 436px; height: 101px;
    background: var(--teal-band);
    clip-path: polygon(0 0, 416px 0, 436px 100%, 0 100%);
    padding: 18px 0 0 46px;
  }
  .name-band__name { font-size: 39px; font-weight: 600; line-height: 1.1; letter-spacing: -0.5px; }
  .name-band__name .last { color: var(--name-dark); }
  .name-band__role { font-size: 21px; font-weight: 300; color: var(--name-dark); line-height: 1.3; }

  .contact { position: absolute; left: 39px; display: flex; align-items: center; gap: 20px; font-size: 21px; font-weight: 500; }
  .contact__icon { width: 42px; height: 42px; flex: none; }
  .contact--phone { top: 287px; }
  .contact--mail { top: 356px; }
  .contact--web { top: 426px; }

  .divider { position: absolute; left: 495px; top: 283px; width: 2px; height: 212px; background: var(--teal); }

  .brand { position: absolute; display: flex; flex-direction: column; align-items: center; transform: translateX(-50%); }
  .brand__dot { border-radius: 50%; background: var(--teal); }
  .brand__name { font-weight: 500; margin-top: 10px; white-space: nowrap; color: var(--white); }
  .card--back .brand { left: 744px; top: 58px; }
  .card--back .brand__dot { width: 96px; height: 96px; }
  .card--back .brand__name { font-size: 24px; }

  .tagline { position: absolute; font-weight: 500; white-space: nowrap; transform: translateX(-50%); color: var(--white); }
  .card--back .tagline { left: 744px; top: 278px; font-size: 22px; }

  .services { position: absolute; left: 0; top: 0; list-style: none; font-weight: 500; font-size: 22px; }
  .services li { position: absolute; white-space: nowrap; padding-left: 20px; }
  .services li::before {
    content: ""; position: absolute; left: 0; top: 50%;
    width: 8px; height: 8px; margin-top: -4px; border-radius: 50%; background: var(--teal);
  }

  /* front side */
  .card--front .brand { left: 480px; top: 92px; }
  .card--front .brand__dot { width: 112px; height: 112px; }
  .card--front .brand__name { font-size: 28px; }
  .card--front .tagline { left: 480px; top: 325px; font-size: 32px; }
</style>
</head>
<body>

<section class="card card--back" aria-label="Card back">
  <div class="name-band">
    <p class="name-band__name">Darren <span class="last">Whitlow</span></p>
    <p class="name-band__role">Health &amp; Wellbeing Life Coach</p>
  </div>

  <div class="contact contact--phone">
    <svg class="contact__icon" viewBox="0 0 42 42" aria-hidden="true">
      <circle cx="21" cy="21" r="21" fill="#1a9a86"/>
      <path d="M14 11c1.5-1 3-.5 3.6.8l1.6 3.4c.4.9 0 1.8-.7 2.3l-1.3.9c.9 2.4 2.9 4.6 5.4 5.6l1-1.3c.6-.7 1.5-.9 2.3-.5l3.3 1.7c1.2.6 1.6 2.2.6 3.6-1.4 1.9-3.7 2.6-6 1.6-5-2.1-9-6.3-10.9-11.3-.9-2.4-.1-4.8 1.1-6.8z" fill="#fff"/>
    </svg>
    <span>0491 372 615</span>
  </div>
  <div class="contact contact--mail">
    <svg class="contact__icon" viewBox="0 0 42 42" aria-hidden="true">
      <circle cx="21" cy="21" r="21" fill="#1a9a86"/>
      <rect x="11" y="14" width="20" height="14" rx="1.5" fill="#fff"/>
      <path d="M11.5 14.8 21 22l9.5-7.2M11.5 27.3l7-6M30.5 27.3l-7-6" fill="none" stroke="#1a9a86" stroke-width="1.6"/>
    </svg>
    <span>darren@brightcoreliving.example</span>
  </div>
  <div class="contact contact--web">
    <svg class="contact__icon" viewBox="0 0 42 42" aria-hidden="true">
      <circle cx="21" cy="21" r="21" fill="#1a9a86"/>
      <circle cx="21" cy="21" r="10" fill="none" stroke="#fff" stroke-width="2"/>
      <ellipse cx="21" cy="21" rx="4.5" ry="10" fill="none" stroke="#fff" stroke-width="1.8"/>
      <path d="M11 21h20M13 16h16M13 26h16" stroke="#fff" stroke-width="1.6"/>
    </svg>
    <span>www.brightcoreliving.example</span>
  </div>

  <div class="divider"></div>

  <div class="brand">
    <span class="brand__dot"></span>
    <span class="brand__name">Brightcore Living</span>
  </div>
  <p class="tagline">The journey home starts with you</p>

  <ul class="services">
    <li style="left:594px; top:398px;">Seminars</li>
    <li style="left:776px; top:398px;">Coaching</li>
    <li style="left:594px; top:442px;">Workshops</li>
    <li style="left:776px; top:442px;">Podcasts</li>
  </ul>
</section>

<section class="card card--front" aria-label="Card front">
  <div class="brand">
    <span class="brand__dot"></span>
    <span class="brand__name">Brightcore Living</span>
  </div>
  <p class="tagline">The journey home starts with you</p>
  <ul class="services">
    <li style="left:164px; top:464px;">Seminars</li>
    <li style="left:342px; top:464px;">Coaching</li>
    <li style="left:498px; top:464px;">Workshops</li>
    <li style="left:680px; top:464px;">Podcasts</li>
  </ul>
</section>

</body>
</html>
```